KRT Info Brochure

We need a brochure design for a new not-for-profit organisation that is aimed at providing homeless people with a residence that also provides counselling and vocational training to assist them to find suitable employment at the end of the program.
PLEASE NOTE:
Brochure to be A4.
I know the brochure is quite long, it is really a booklet, but please note that it does not have to have a lot of work done on it, I just want it to look professional and the front cover and inside page to look good.
Also please leave about 2-3 pages at the end as I will be adding in some architect drawings.
Please add in a last page with Contact written at the bottom - we will fill that in later. So please ensure it is editable in PDF.
Thank you so much.
Cheers
Marta

```html
<!DOCTYPE html>
<html lang="en">
<head>
<meta charset="utf-8">
<title>KRT Legacy Foundation – Brochure Cover and Contents</title>
<link rel="stylesheet" href="https://fonts.googleapis.com/css2?family=Cinzel:wght@400;600&family=Source+Sans+3:wght@400;600;700&display=swap">
<style>
  :root {
    --stage: #d8d5d1;
    --paper: #ffffff;
    --blue: #1a66b3;
    --blue-deep: #124f95;
    --blue-light: #3a86d0;
    --gold: #f7b52a;
    --gold-light: #fde3a6;
    --charcoal: #3b3b3e;
    --ink: #333438;
    --muted: #707276;
    --swirl-cream: #ece2c8;
    --swirl-grey: #d9d9dc;
    --serif: "Cinzel", serif;
    --sans: "Source Sans 3", sans-serif;
  }
  * { box-sizing: border-box; margin: 0; padding: 0; }
  html, body { width: 877px; height: 1200px; overflow: hidden; background: var(--stage); }
  .canvas { position: relative; width: 877px; height: 1200px; overflow: hidden; font-family: var(--sans); }

  .spread { position: absolute; left: 79px; width: 732px; height: 518px; display: flex; }
  .spread--covers { top: 83px; }
  .spread--inside { top: 617px; }
  .page { position: relative; width: 366px; height: 100%; background: var(--paper); overflow: hidden; }

  /* Back cover */
  .back-swirl { position: absolute; left: 150px; top: 0; width: 120px; height: 300px;
    background: linear-gradient(100deg, transparent 20%, var(--swirl-cream) 50%, transparent 80%); opacity: .7; }
  .wordmark { font-family: var(--sans); font-weight: 700; color: var(--gold); letter-spacing: 1px; display: flex; align-items: center; gap: 6px; }
  .wordmark__dot { width: 14px; height: 14px; border-radius: 50%; background: var(--gold); }
  .back-cover .wordmark { position: absolute; left: 0; right: 0; top: 412px; justify-content: center; font-size: 22px; }
  .back-rule { position: absolute; left: 34px; right: 34px; top: 464px; border-top: 1px solid #cfcfd2; }
  .back-contact { position: absolute; left: 0; right: 0; top: 470px; text-align: center; font-size: 6px; line-height: 1.7; color: var(--muted); }
  .back-web { position: absolute; left: 0; right: 0; top: 495px; text-align: center; font-size: 7px; letter-spacing: 1px; color: var(--gold); }

  /* Front cover */
  .front-cover svg { position: absolute; inset: 0; }
  .front-cover .wordmark { position: absolute; left: 108px; top: 322px; font-size: 26px; }
  .front-title { position: absolute; left: 0; right: 0; bottom: 12px; text-align: center; font-family: var(--serif); color: #fff; font-size: 15px; letter-spacing: 2.5px; }

  /* Inside left */
  .inside-left { background: linear-gradient(90deg, var(--blue-deep), var(--blue) 55%, var(--blue-light)); }
  .inside-swirl { position: absolute; left: 110px; top: 0; width: 150px; height: 420px;
    background: linear-gradient(95deg, transparent 25%, rgba(255,255,255,.28) 50%, transparent 75%); }
  .inside-title { position: absolute; left: 0; right: 0; top: 408px; text-align: center; font-family: var(--serif); color: #fff; font-size: 23px; line-height: 1.3; letter-spacing: 1px; }

  /* Contents */
  .contents-swirl { position: absolute; right: 0; top: 0; width: 150px; height: 518px;
    background: linear-gradient(105deg, transparent 30%, var(--swirl-cream) 55%, var(--swirl-grey) 70%, transparent 90%); opacity: .8; }
  .contents-heading { position: absolute; left: 25px; top: 36px; font-size: 22px; font-weight: 700; color: var(--blue); }
  .contents-list { position: absolute; left: 25px; top: 78px; width: 177px; list-style: none; font-size: 5.6px; color: var(--ink); }
  .toc-bar { display: flex; justify-content: space-between; align-items: center; height: 9px; padding: 0 5px; margin-top: 6px; color: #fff; font-weight: 700; background: linear-gradient(90deg, var(--blue-deep), var(--blue-light)); border-radius: 1px; }
  .toc-bar:first-child { margin-top: 0; }
  .toc-bar--summary { background: var(--charcoal); }
  .toc-row { display: flex; align-items: baseline; height: 8.6px; padding: 0 5px 0 8px; }
  .toc-row--deep { padding-left: 20px; }
  .toc-row__num { width: 14px; flex: none; }
  .toc-row__dots { flex: 1; border-bottom: 0.6px dotted #a8a9ad; margin: 0 3px; }
  .toc-row--attach .toc-row__num { width: 38px; }
</style>
</head>
<body>
<div class="canvas">

  <section class="spread spread--covers">
    <div class="page back-cover">
      <div class="back-swirl" role="img" aria-label="Soft cream swirling ribbon decoration"></div>
      <div class="wordmark"><span class="wordmark__dot"></span>KRT</div>
      <div class="back-rule"></div>
      <p class="back-contact">KRT Legacy Foundation, Suite 800, Cityname, Country name.<br>Tel: 012 555 0147 &nbsp;&nbsp; Email: info@krtlegacyfoundation.org</p>
      <p class="back-web">www.krtlegacyfoundation.org</p>
    </div>

    <div class="page front-cover">
      <svg viewBox="0 0 366 518" width="366" height="518" aria-hidden="false">
        <defs>
          <linearGradient id="goldWash" x1="0" y1="0" x2="0" y2="1">
            <stop offset="0" stop-color="var(--gold-light)"/>
            <stop offset="1" stop-color="var(--gold)"/>
          </linearGradient>
          <linearGradient id="blueWash" x1="0" y1="0" x2="0" y2="1">
            <stop offset="0" stop-color="var(--blue)"/>
            <stop offset="1" stop-color="var(--blue-deep)"/>
          </linearGradient>
        </defs>
        <path role="img" aria-label="Warm yellow panel with a house roof and window illustration"
              d="M0 0 H366 V160 C340 185 310 235 255 245 C185 255 70 215 0 228 Z" fill="url(#goldWash)"/>
        <path d="M0 385 C80 368 175 425 262 398 C322 378 348 330 366 300 V518 H0 Z" fill="url(#blueWash)"/>
      </svg>
      <div class="wordmark"><span class="wordmark__dot"></span>KRT</div>
      <h1 class="front-title">KRT LEGACY FOUNDATION</h1>
    </div>
  </section>

  <section class="spread spread--inside">
    <div class="page inside-left">
      <div class="inside-swirl" role="img" aria-label="Translucent white swirling ribbon decoration"></div>
      <h2 class="inside-title">KRT LEGACY<br>FOUNDATION</h2>
    </div>

    <div class="page contents-page">
      <div class="contents-swirl" role="img" aria-label="Cream and grey swirling ribbon decoration"></div>
      <h2 class="contents-heading">Contents</h2>
      <ol class="contents-list">
        <li class="toc-bar toc-bar--summary"><span>Executive Summary</span><span>5</span></li>
        <li class="toc-bar"><span>1.&nbsp;&nbsp; HOMELESSNESS</span><span>6</span></li>
        <li class="toc-bar"><span>2.&nbsp;&nbsp; PROGRAM OVERVIEW</span><span>7</span></li>
        <li class="toc-row"><span class="toc-row__num">2.1</span>Physiological<span class="toc-row__dots"></span>7</li>
        <li class="toc-row"><span class="toc-row__num">2.2</span>Psychological<span class="toc-row__dots"></span>7</li>
        <li class="toc-row"><span class="toc-row__num">2.3</span>Learning/Training<span class="toc-row__dots"></span>7</li>
        <li class="toc-row"><span class="toc-row__num">2.4</span>Special Needs<span class="toc-row__dots"></span>8</li>
        <li class="toc-row"><span class="toc-row__num">2.5</span>Vocational Education<span class="toc-row__dots"></span>8</li>
        <li class="toc-row"><span class="toc-row__num">2.6</span>Fitting back into Society<span class="toc-row__dots"></span>8</li>
        <li class="toc-row"><span class="toc-row__num">2.7</span>Outreach / After Care Program<span class="toc-row__dots"></span>8</li>
        <li class="toc-row"><span class="toc-row__num">2.8</span>Family Groups<span class="toc-row__dots"></span>9</li>
        <li class="toc-row"><span class="toc-row__num">2.9</span>Young People<span class="toc-row__dots"></span>9</li>
        <li class="toc-row"><span class="toc-row__num">2.10</span>Older People<span class="toc-row__dots"></span>9</li>
        <li class="toc-row"><span class="toc-row__num">2.11</span>Alcohol &amp; Drug Dependencies<span class="toc-row__dots"></span>10</li>
        <li class="toc-bar"><span>3.&nbsp;&nbsp; OPERATIONS</span><span>11</span></li>
        <li class="toc-row"><span class="toc-row__num">3.1</span>Management<span class="toc-row__dots"></span>11</li>
        <li class="toc-row"><span class="toc-row__num">3.2</span>Business Location<span class="toc-row__dots"></span>11</li>
        <li class="toc-row"><span class="toc-row__num">3.3</span>Foundation Management<span class="toc-row__dots"></span>11</li>
        <li class="toc-row"><span class="toc-row__num">3.4</span>KRT Staff<span class="toc-row__dots"></span>12</li>
        <li class="toc-row"><span class="toc-row__num">3.5</span>Self Sustainment<span class="toc-row__dots"></span>12</li>
        <li class="toc-row"><span class="toc-row__num">3.6</span>Timeframes<span class="toc-row__dots"></span>13</li>
        <li class="toc-row"><span class="toc-row__num">3.7</span>Marketing and Publicity<span class="toc-row__dots"></span>13</li>
        <li class="toc-bar"><span>4.&nbsp;&nbsp; THE PROGRAM PRACTICALLY</span><span>14</span></li>
        <li class="toc-row"><span class="toc-row__num">4.1</span>Work Task<span class="toc-row__dots"></span>15</li>
        <li class="toc-row"><span class="toc-row__num">4.2</span>Snapshot of a day in the Program<span class="toc-row__dots"></span>16</li>
        <li class="toc-row"><span class="toc-row__num">4.3</span>Logistics<span class="toc-row__dots"></span>16</li>
        <li class="toc-bar"><span>5.&nbsp;&nbsp; THE FUTURE</span><span>17</span></li>
        <li class="toc-row"><span class="toc-row__num">5.1</span>Complementary Businesses<span class="toc-row__dots"></span>17</li>
        <li class="toc-row toc-row--deep"><span class="toc-row__num">5.1.1</span>Phase 1<span class="toc-row__dots"></span>17</li>
        <li class="toc-row toc-row--deep"><span class="toc-row__num">5.1.2</span>Phase 2<span class="toc-row__dots"></span>18</li>
        <li class="toc-row toc-row--deep"><span class="toc-row__num">5.1.3</span>Phase 3<span class="toc-row__dots"></span>18</li>
        <li class="toc-row toc-row--deep"><span class="toc-row__num">5.1.4</span>Phase 4<span class="toc-row__dots"></span>18</li>
        <li class="toc-row toc-row--deep"><span class="toc-row__num">5.1.5</span>Phase 5<span class="toc-row__dots"></span>19</li>
        <li class="toc-row"><span class="toc-row__num">5.2</span>The Long Term<span class="toc-row__dots"></span>19</li>
        <li class="toc-bar"><span>6.&nbsp;&nbsp; THE FINANCES</span><span>20</span></li>
        <li class="toc-row"><span class="toc-row__num">6.1</span>Funding<span class="toc-row__dots"></span>20</li>
        <li class="toc-row"><span class="toc-row__num">6.2</span>Income<span class="toc-row__dots"></span>20</li>
        <li class="toc-row"><span class="toc-row__num">6.3</span>Fundraising<span class="toc-row__dots"></span>21</li>
        <li class="toc-row toc-row--attach" style="margin-top:4px"><span class="toc-row__num">Attachment 1:</span>S.W.O.T. analysis<span class="toc-row__dots"></span>22</li>
        <li class="toc-row toc-row--attach"><span class="toc-row__num">Attachment 2:</span>Learning For Residents<span class="toc-row__dots"></span>23</li>
      </ol>
    </div>
  </section>

</div>
</body>
</html>
```